Business Card for my New Brokerage

Looking to get a business card design for my new Real Estate Brokerage.
I want it with Picture, Phone Number, Email, Website, Office Address
Name and Designation. Please add logo too.

Target Market(s)

Real Estate Investors or Home Buyers

Industry/Entity Type

Real Estate

Contact Information for Business Card

Name, Email, Phone Number, website, email, office address

Colors
EB3D1F
EC4F4E
F09395
F8D3D4
FCEDEE

Requirements
Must have
• Minimalistic, Clean, Modern, Photo
Nice to have
• White and Red Colors

```html
<!DOCTYPE html>
<html lang="en">
<head>
<meta charset="utf-8">
<title>Lumen Realty Inc – Business Card</title>
<link rel="stylesheet" href="https://fonts.googleapis.com/css2?family=Montserrat:wght@600&family=Lato:wght@400;700&display=swap">
<style>
  :root {
    --backdrop: #a3a3a3;
    --brand-red: #e00000;
    --gold: #e9c35a;
    --gold-light: #f6dd8c;
    --white: #ffffff;
    --photo-wall: #ecebe8;
    --photo-suit: #3a3a3a;
  }
  html, body {
    margin: 0;
    width: 1200px;
    height: 1200px;
    overflow: hidden;
    background: var(--backdrop);
  }
  .card {
    position: absolute;
    top: 303px;
    width: 369px;
    height: 593px;
    background: var(--white);
    box-shadow: 3px 4px 6px rgba(0,0,0,0.35);
    overflow: hidden;
  }
  .card--front { left: 201px; }
  .card--back { left: 599px; width: 364px; }
  .card svg { display: block; }

  .brand-name {
    font-family: "Montserrat", sans-serif;
    font-weight: 600;
    fill: var(--brand-red);
  }

  .portrait {
    position: absolute;
    left: 0;
    top: 8px;
    width: 100%;
    height: 323px;
    background: linear-gradient(180deg, var(--photo-wall) 0%, var(--photo-wall) 60%, #b9b5ae 80%, var(--photo-suit) 100%);
  }
  .contact-panel {
    position: absolute;
    left: 0;
    top: 331px;
    width: 100%;
    height: 262px;
    background: var(--brand-red);
    color: var(--white);
    font-family: "Lato", sans-serif;
    text-align: center;
  }
  .contact-panel p { margin: 0; position: absolute; left: 0; width: 100%; line-height: 1; }
  .agent-name { top: 37px; font-size: 24px; font-weight: 700; letter-spacing: 0.3px; }
  .agent-title { top: 64px; font-size: 17px; }
  .divider {
    position: absolute;
    left: 152px;
    width: 59px;
    height: 1px;
    background: var(--white);
  }
  .divider--upper { top: 94px; }
  .divider--lower { top: 184px; }
  .contact-line { font-size: 17px; }
  .contact-phone { top: 107px; }
  .contact-email { top: 130px; }
  .contact-web { top: 153px; }
  .address-line { font-size: 17px; }
  .address-street { top: 196px; }
  .address-country { top: 218px; }
</style>
</head>
<body>
  <section class="card card--front">
    <svg width="369" height="593" viewBox="0 0 369 593">
      <defs>
        <linearGradient id="patternTone" x1="0" y1="0" x2="1" y2="1">
          <stop offset="0" stop-color="#e00000"/>
          <stop offset="0.5" stop-color="#e4201a"/>
          <stop offset="1" stop-color="#e00000"/>
        </linearGradient>
      </defs>
      <rect class="star-pattern" width="369" height="593" fill="url(#patternTone)" role="img" aria-label="Repeating gold four-point star pattern on red"/>
      <polygon class="logo-field" points="0,328 369,63 369,576" fill="#ffffff"/>
      <text class="brand-name" x="190" y="340" text-anchor="middle" font-size="64">LUMEN</text>
      <text class="brand-name" x="193" y="375" text-anchor="middle" font-size="18" letter-spacing="4">REALTY INC</text>
    </svg>
  </section>

  <section class="card card--back">
    <div class="portrait" role="img" aria-label="Portrait photo of the agent in a dark suit against a light wall"></div>
    <div class="contact-panel">
      <p class="agent-name">MARCUS HALE</p>
      <p class="agent-title">Managing Director</p>
      <span class="divider divider--upper"></span>
      <p class="contact-line contact-phone">044-123 456 789</p>
      <p class="contact-line contact-email">info@webname.com</p>
      <p class="contact-line contact-web">www.websitename.com</p>
      <span class="divider divider--lower"></span>
      <p class="address-line address-street">421, Address line here</p>
      <p class="address-line address-country">Country Name, 45452</p>
    </div>
  </section>
</body>
</html>
```